2 x Digitize Logo | 2 x Business Cards | 2 x Fridge Magnets

We require 6 deliverables:
1. Residential logo redrawn (same just high quality for large print format).
2. Corporate logo redrawn (minor changes to wording and high quality for large print format).
3. New business card design for Furniture Removals (residential)
4. New business card design for Corporate Relocations (business)
5. New Fridge magnet for Furniture removals (residential)
6. New fridge magnet for Corporate Relocations (business)
1. Residential Logo
a. We require the logo to be translated into a high quality digital image with no modifications.
(see attached resilogo.jpg)
2. Residential Logo
a. We require the logo to be edited (add the word corporate relocations) be translated into a high quality digital image.
(see attached corplogo.jpg)
3. Using the resilogo please make a new business card for our business.
a. Please see the web site https://www.larkbendcarters.com.au for colours and inspiration.
b. The residential business card needs the following information:
i. Business Name (using the residential logo).
ii. Free Call: 1800 LB Cart (the L, B and Cart much be the same colour as the logo).
iii. Website: www.LarkbendCarters.com.au
iv. Address: 4/17 Ormsdale Court, VIC 3264
v. Email: cart@LarkbendCarters.com.au
vi. backof Card:
Review our service
www.PennantOrbit.com.au
Services: Local, Country, Interstate | Furniture Removals | Piano, Billiard Tables & Antiques
4. Using the corplogo please make a new business card for our business.
b. The corporate business card needs the following information:
i. Business Name (using the corporate logo).
v. Email: corporate@LarkbendCarters.com.au
vi. Back of Card:
Review our service
www.PennantOrbit.com.au
Services: Corporate relocations | Office equipment moves | Packing Service | Packing Materials
5. Using the resilogo please make a new fridge magent for our business.
b. The residential fidge magnet needs the following information:
iv. Services: Local, Country, Interstate | Furniture Removals | Piano, Billiard Tables & Antiques
6. Using the corplogo please make a new fridge magent for our business.
b. The corporate fidge magnet needs the following information:
iv. Services: Local, Country, Interstate | Corporate relocations
Target Market(s)
Residential Furniture Removals and Corporate Office relocations
Industry/Entity Type
Business
Contact Information for Business Card
Please see full brief for six items required
Requirements
Must have
- Clean simple, easy to read
Nice to have
- fresh, stand out, eye catching
Should not have
- plain, standard, boring, general

```html
<!DOCTYPE html>
<html lang="en">
<head>
<meta charset="utf-8">
<title>Larkbend Carters – Business Cards</title>
<link rel="stylesheet" href="https://fonts.googleapis.com/css2?family=Source+Sans+3:wght@400;600&display=swap">
<style>
  :root {
    --board-dark: #4a4a4a;
    --board-light: #7d7d7d;
    --card: #ffffff;
    --ink: #2b2b2b;
    --rule: #555555;
    --brand-yellow: #f2b400;
    --brand-red: #c8101e;
    --brand-green: #22a84a;
    --deep-green: #12803a;
  }
  * { box-sizing: border-box; margin: 0; padding: 0; }
  html, body { width: 1165px; height: 1200px; overflow: hidden; }
  body {
    font-family: "Source Sans 3", Arial, sans-serif;
    background: radial-gradient(ellipse at 40% 10%, var(--board-light), var(--board-dark) 85%);
    position: relative;
    color: var(--ink);
  }
  .card {
    position: absolute;
    top: 185px;
    width: 321px;
    height: 519px;
    background: var(--card);
    box-shadow: 2px 3px 4px rgba(0,0,0,.45);
    text-align: center;
  }
  .card--residential { left: 252px; }
  .card--corporate { left: 624px; }
  .card__call {
    position: absolute; top: 40px; left: 0; right: 0;
    font-size: 19.5px; font-weight: 600; line-height: 26px;
  }
  .card__web {
    position: absolute; top: 116px; left: 0; right: 0;
    font-size: 16px;
  }
  .card__brand {
    position: absolute; left: 0; right: 0;
    display: flex; justify-content: center; align-items: center; gap: 8px;
    font-size: 27px; font-weight: 600; letter-spacing: .5px;
  }
  .card--residential .card__brand { top: 230px; color: var(--brand-red); }
  .card--corporate .card__brand { top: 230px; color: var(--brand-red); }
  .brand-mark { width: 14px; height: 14px; display: inline-block; }
  .card--residential .brand-mark { background: var(--brand-green); }
  .card--corporate .brand-mark { background: var(--deep-green); border-radius: 50%; }
  .card__services-head {
    position: absolute; top: 354px; left: 40px; right: 40px;
    display: flex; align-items: center; gap: 6px;
    font-size: 20px; letter-spacing: .3px;
  }
  .card__services-head::before,
  .card__services-head::after {
    content: ""; flex: 1; height: 1px; background: var(--rule);
  }
  .card__services {
    position: absolute; top: 393px; left: 0; right: 0;
    list-style: none; font-size: 18px; line-height: 27.5px;
  }
  .card__band {
    position: absolute; left: 0; right: 0; bottom: 0; height: 19px;
  }
  .card--residential .card__band { background: var(--brand-green); }
  .card--corporate .card__band { background: var(--brand-red); }
  .c-yellow { color: var(--brand-yellow); }
  .c-red { color: var(--brand-red); }
  .c-green { color: var(--brand-green); }
  .c-deepgreen { color: var(--deep-green); }
  .truck-photo {
    position: absolute; left: 341px; top: 759px; width: 521px; height: 321px;
    background: linear-gradient(160deg, #d9dde2 0%, #f3f3f3 45%, #bfc3c7 75%, #5c5e60 100%);
    box-shadow: 2px 3px 4px rgba(0,0,0,.45);
  }
</style>
</head>
<body>
  <section class="card card--residential">
    <p class="card__call">Free Call<br>1800 <span class="c-yellow">L</span><span class="c-red">B</span> <span class="c-green">Cart</span> / 1800 52 41 87</p>
    <p class="card__web">www.larkbendcarters.com.au</p>
    <div class="card__brand"><span class="brand-mark"></span>LARKBEND CARTERS</div>
    <h2 class="card__services-head">SERVICES</h2>
    <ul class="card__services">
      <li>Local, Country, Interstate</li>
      <li>Furniture Removals</li>
      <li>Piano, Billiard Tables &amp; Antiques</li>
    </ul>
    <div class="card__band"></div>
  </section>

  <section class="card card--corporate">
    <p class="card__call">Free Call<br>1800 <span class="c-deepgreen">L</span><span class="c-red">B</span> <span class="c-red">Cart</span> / 1800 52 41 87</p>
    <p class="card__web">www.larkbendcarters.com.au</p>
    <div class="card__brand"><span class="brand-mark"></span>LARKBEND CARTERS</div>
    <h2 class="card__services-head">SERVICES</h2>
    <ul class="card__services">
      <li>Corporate relocations</li>
      <li>Office equipment moves</li>
      <li>Packing Service | Packing Materials</li>
    </ul>
    <div class="card__band"></div>
  </section>

  <div class="truck-photo" role="img" aria-label="Photo of a white removal truck carrying the company branding, services and phone number on its box body"></div>
</body>
</html>
```